Construction company business card

One side to be the logo with the company name, The other side I would like: (Tomas verbick) Project manager 41 barrow crescent hallam 52917306224783(03) 9703 2428Info@gudeljgroup.comAnd then maybe a couple dot points saying what we do:Construction (commercial & industrial) Civil construction

Anything else please contact me!
Maybe curved st one edge of the card

Target Market(s)

Older clientele

Industry/Entity Type

Construction Company

Contact Information for Business Card

Read above

Colors
3277b5
1b1b1b
9d9d9d

Requirements
Must have
• Use my logo on one side
Nice to have
• Read above
Should not have
• Read above

```html
<!DOCTYPE html>
<html lang="en">
<head>
<meta charset="utf-8">
<title>Stonefield Property Group – Business Card</title>
<link rel="stylesheet" href="https://fonts.googleapis.com/css2?family=Lato:wght@700&family=Open+Sans:wght@400;700&display=swap">
<style>
  :root {
    --brand-blue: #3277b5;
    --ink: #1b1b1b;
    --steel: #9d9d9d;
    --paper: #ffffff;
    --backdrop: #e6e4e0;
    --rule-light: rgba(255,255,255,0.6);
  }
  * { margin: 0; padding: 0; box-sizing: border-box; }
  html, body { width: 1200px; height: 900px; overflow: hidden; }
  body {
    background: var(--backdrop);
    position: relative;
    font-family: "Open Sans", Arial, sans-serif;
  }
  .card {
    position: absolute;
    left: 330px;
    width: 556px;
    height: 343px;
    box-shadow: 2px 3px 6px rgba(0,0,0,0.35);
  }
  /* Contact side */
  .card--contact {
    top: 90px;
    background: var(--brand-blue);
    color: var(--paper);
    text-align: center;
  }
  .contact__name {
    position: absolute; top: 84px; left: 0; right: 0;
    font-family: "Lato", Arial, sans-serif;
    font-weight: 700; font-size: 21px; letter-spacing: 0.3px;
    text-transform: uppercase; line-height: 24px;
  }
  .contact__role {
    position: absolute; top: 105px; left: 0; right: 0;
    font-size: 16px; line-height: 20px;
  }
  .contact__icons {
    position: absolute; top: 133px; left: 190px; width: 176px; height: 20px;
  }
  .contact__details {
    position: absolute; top: 161px; left: 0; right: 0;
    font-size: 16px; line-height: 20.5px;
  }
  .contact__rule {
    position: absolute; top: 233px; left: 190px; width: 176px;
    height: 1px; background: var(--rule-light);
  }
  .contact__address {
    position: absolute; top: 243px; left: 0; right: 0;
    font-size: 16px; line-height: 19.5px;
  }
  /* Brand side */
  .card--brand {
    top: 469px;
    background: var(--paper);
    text-align: center;
  }
  .brand__mark {
    position: absolute; top: 62px; left: 50%;
    width: 118px; height: 118px; margin-left: -59px;
    border-radius: 50%; background: var(--brand-blue);
  }
  .brand__name {
    position: absolute; top: 203px; left: 0; right: 0;
    font-weight: 700; color: var(--brand-blue);
    font-size: 29px; line-height: 30px; letter-spacing: 0.5px;
    text-transform: uppercase;
  }
  .brand__name small {
    display: block; font-size: 13px; line-height: 18px; letter-spacing: 4.5px;
  }
  .brand__rule {
    position: absolute; top: 279px; left: 47px; width: 466px;
    height: 1px; background: #c4c4c4;
  }
  .brand__services {
    position: absolute; top: 287px; left: 0; right: 0;
    list-style: none; font-size: 16.5px; color: var(--ink);
    display: flex; justify-content: center; gap: 6px;
  }
  .brand__services li::before {
    content: ""; display: inline-block; width: 8px; height: 8px;
    border-radius: 50%; background: var(--brand-blue);
    margin-right: 6px; vertical-align: 2px;
  }
</style>
</head>
<body>
  <section class="card card--contact">
    <h1 class="contact__name">Tomas Verbick</h1>
    <p class="contact__role">Project manager</p>
    <svg class="contact__icons" viewBox="0 0 176 20" aria-hidden="true">
      <line x1="0" y1="10" x2="56" y2="10" stroke="rgba(255,255,255,0.6)" stroke-width="1"/>
      <line x1="120" y1="10" x2="176" y2="10" stroke="rgba(255,255,255,0.6)" stroke-width="1"/>
      <g fill="#ffffff">
        <circle cx="66" cy="10" r="9"/>
        <circle cx="87" cy="10" r="9"/>
        <circle cx="108" cy="10" r="9"/>
      </g>
      <g fill="none" stroke="#3277b5" stroke-width="1.5" stroke-linejoin="round">
        <path d="M61 9 q5 -4 10 0 M62.5 9 l1 4 h5 l1 -4"/>
        <rect x="84" y="5" width="6" height="10" rx="1"/>
        <rect x="103.5" y="6.5" width="9" height="7"/>
        <path d="M103.5 6.5 l4.5 4 l4.5 -4"/>
      </g>
    </svg>
    <p class="contact__details">7306224783<br>(03) 9418 6573<br>Info@verbickgroup.com</p>
    <div class="contact__rule"></div>
    <p class="contact__address">41 barrow crescent<br>dunmore 5291</p>
  </section>

  <section class="card card--brand">
    <div class="brand__mark" aria-hidden="true"></div>
    <h2 class="brand__name">Stonefield<small>Property Group</small></h2>
    <div class="brand__rule"></div>
    <ul class="brand__services">
      <li>Construction (commercial &amp; industrial)</li>
      <li>Civil construction</li>
    </ul>
  </section>
</body>
</html>
```